Specialised investor in e-mobility and energy wants business card design

We need a business card design that fits our existing corporate design. <The look and feel must be 'sharp'/'clean', dynamic, communicate momentum, professionalism etc (as one would imagine from a firm in the financial sector). We like the idea of a reverse-side of the card that includes the logo, and the name and contact details on the other. We expect the deliverable to be whatever format might be required to be able to get cards printed directly by a service such as kelmo press. Our website is www.zub.capital

```html
<!DOCTYPE html>
<html lang="en">
<head>
<meta charset="utf-8">
<title>Zub Capital – Business Card</title>
<link href="https://fonts.googleapis.com/css2?family=Jost:wght@400;500;600;800&display=swap" rel="stylesheet">
<style>
  :root {
    --page-bg: #e6e6e6;
    --card-white: #f5f5f5;
    --forest: #2d4a22;
    --leaf: #7fae4b;
    --emboss: #3e6630;
    --ink-light: #ffffff;
  }
  * { margin: 0; padding: 0; box-sizing: border-box; }
  html, body {
    width: 1200px; height: 1200px; overflow: hidden;
    background: var(--page-bg);
    font-family: "Jost", sans-serif;
  }
  .card {
    position: absolute;
    left: 262px;
    width: 686px; height: 392px;
    border-radius: 26px;
    overflow: hidden;
  }
  .card--front { top: 165px; background: var(--card-white); }
  .card--back { top: 653px; background: var(--forest); }
  .card__waves { position: absolute; inset: 0; width: 100%; height: 100%; }

  .brand-name {
    position: absolute; left: 55px; top: 62px;
    font-size: 52px; font-weight: 500; color: var(--forest);
    letter-spacing: 0.5px; line-height: 1;
  }
  .holder { position: absolute; left: 58px; top: 171px; }
  .holder__name {
    font-size: 27px; font-weight: 800; color: var(--forest);
    letter-spacing: 0.5px; line-height: 1;
  }
  .holder__role {
    margin-top: 6px; font-size: 16px; font-weight: 400; color: var(--leaf);
    letter-spacing: 0.3px;
  }
  .contact {
    position: absolute; right: 42px; top: 245px;
    text-align: right; color: var(--ink-light);
    font-size: 17px; font-weight: 400; letter-spacing: 0.2px;
  }
  .contact__city { line-height: 1; margin-bottom: 16px; }
  .contact__line {
    display: flex; justify-content: flex-end; align-items: center;
    gap: 8px; line-height: 22px; margin-right: -20px;
  }
  .contact__icon { width: 12px; height: 12px; fill: var(--leaf); }
  .contact__web {
    margin-top: 12px; margin-right: -4px;
    font-weight: 600; color: var(--leaf);
  }

  .back-mark {
    position: absolute; left: 0; right: 0; top: 160px;
    text-align: center; line-height: 1;
    font-size: 66px; font-weight: 500; color: var(--emboss);
    letter-spacing: 1px;
  }
</style>
</head>
<body>
  <section class="card card--front">
    <svg class="card__waves" viewBox="0 0 686 392" preserveAspectRatio="none" aria-hidden="true">
      <path d="M0,262 C180,330 420,290 686,52 L686,392 L0,392 Z" fill="var(--leaf)"/>
      <path d="M0,259 C180,336 430,305 686,100 L686,392 L0,392 Z" fill="var(--forest)" stroke="#ffffff" stroke-width="2"/>
    </svg>

    <div class="brand-name">Zub Capital</div>

    <div class="holder">
      <div class="holder__name">PETER HALVORSEN</div>
      <div class="holder__role">Managing Director</div>
    </div>

    <div class="contact">
      <div class="contact__city">Geneva, Switzerland</div>
      <div class="contact__line">
        <span>+41 79555 0148</span>
        <svg class="contact__icon" viewBox="0 0 24 24" aria-hidden="true">
          <path d="M6.6 10.8a15.1 15.1 0 0 0 6.6 6.6l2.2-2.2a1 1 0 0 1 1-.25 11.4 11.4 0 0 0 3.6.57 1 1 0 0 1 1 1V20a1 1 0 0 1-1 1A17 17 0 0 1 3 4a1 1 0 0 1 1-1h3.5a1 1 0 0 1 1 1c0 1.25.2 2.45.57 3.6a1 1 0 0 1-.25 1z"/>
        </svg>
      </div>
      <div class="contact__line">
        <span>peter@zub.capital</span>
        <svg class="contact__icon" viewBox="0 0 24 24" aria-hidden="true">
          <path d="M2 5h20v14H2z M2 5l10 8 10-8" fill="var(--leaf)"/>
          <path d="M3 6l9 7 9-7" fill="none" stroke="var(--forest)" stroke-width="2"/>
        </svg>
      </div>
      <div class="contact__web">www.zub.capital</div>
    </div>
  </section>

  <section class="card card--back">
    <div class="back-mark">Zub Capital</div>
  </section>
</body>
</html>
```